Garlic Farm for Farm Sales/Restaurant sales

Need a professional, but appealing to agriculture world. We are selling 27 kinds of Organic Garlic from a farm in Simla,CO. I have uploaded logo and business information-we are going to need a template, because I will need to use it for four separate people.
-We are trying to appeal to Farm to table restaurants
-As well as growers/farmers

Target Market(s)

Agriculture Sales/Restaurants-Organic

Industry/Entity Type

Agriculture

Contact Information for Business Card

Want it to look more unique then your average kelto stock card- I want it to look amazing

Font styles to use
Sans Serif

Colors
0455a3
ec1f27
fbed22
ffffff

Requirements
Must have
• Just be creative
Nice to have
• Colorful
Should not have
• plain

```html
<!DOCTYPE html>
<html lang="en">
<head>
<meta charset="utf-8">
<title>Redmesa Garlic – Business Card</title>
<link href="https://fonts.googleapis.com/css2?family=PT+Sans:ital,wght@0,400;0,700;1,400;1,700&display=swap" rel="stylesheet">
<style>
  :root {
    --stage: #141414;
    --navy: #0b2d5e;
    --red: #c8102e;
    --white: #ffffff;
    --ink: #0b2d5e;
  }
  html, body {
    margin: 0;
    padding: 0;
    width: 1200px;
    height: 900px;
    overflow: hidden;
    background: var(--stage);
    font-family: "PT Sans", Arial, sans-serif;
  }
  .canvas {
    position: relative;
    width: 1200px;
    height: 900px;
  }
  .card {
    position: absolute;
    top: 206px;
    width: 275px;
    height: 445px;
    overflow: hidden;
    text-align: center;
  }
  .card--front { left: 315px; background: var(--white); }
  .card--back  { left: 621px; background: var(--navy); }

  .card__arc {
    position: absolute;
    left: 0;
    width: 275px;
    height: 16px;
  }
  .card__arc--top { top: 0; }
  .card__arc--bottom { bottom: 0; }

  .brand {
    position: absolute;
    left: 0;
    width: 100%;
    display: flex;
    flex-direction: column;
    align-items: center;
  }
  .brand__dot {
    border-radius: 50%;
    background: var(--red);
  }
  .brand__name {
    font-weight: 700;
    letter-spacing: 0.5px;
    text-transform: lowercase;
  }
  .card--front .brand { top: 48px; }
  .card--front .brand__dot { width: 78px; height: 78px; }
  .card--front .brand__name { color: var(--ink); font-size: 30px; margin-top: 14px; }

  .card--back .brand { top: 142px; }
  .card--back .brand__dot { width: 92px; height: 92px; }
  .card--back .brand__name { color: var(--white); font-size: 36px; margin-top: 18px; }

  .person {
    position: absolute;
    top: 222px;
    left: 0;
    width: 100%;
  }
  .person__name {
    margin: 0;
    color: var(--red);
    font-size: 23px;
    font-weight: 700;
    font-style: italic;
    line-height: 28px;
  }
  .person__role {
    margin: 0;
    color: var(--ink);
    font-size: 15px;
    font-style: italic;
    line-height: 18px;
  }
  .contact {
    position: absolute;
    top: 282px;
    left: 0;
    width: 100%;
    margin: 0;
    padding: 0;
    list-style: none;
    color: var(--ink);
    font-size: 14px;
    line-height: 18.5px;
  }
  .contact__label { color: var(--red); }
  .address {
    position: absolute;
    top: 367px;
    left: 0;
    width: 100%;
    margin: 0;
    color: var(--ink);
    font-size: 14px;
    line-height: 18.5px;
    font-style: normal;
  }
</style>
</head>
<body>
<main class="canvas">
  <section class="card card--front" aria-label="Business card front">
    <svg class="card__arc card__arc--top" viewBox="0 0 275 16" aria-hidden="true">
      <path d="M68 0 Q137 24 207 0 Z" fill="var(--red)"/>
    </svg>
    <div class="brand">
      <span class="brand__dot" aria-hidden="true"></span>
      <span class="brand__name">redmesa garlic</span>
    </div>
    <div class="person">
      <p class="person__name">lena harper</p>
      <p class="person__role">Owner</p>
    </div>
    <ul class="contact">
      <li><span class="contact__label">P:</span> 555-014-2287</li>
      <li><span class="contact__label">F:</span> (555)-014-7</li>
      <li><span class="contact__label">E:</span> hello@redmesagarlic.com</li>
      <li>www.redmesagarlic.com</li>
    </ul>
    <address class="address">PO Box 720318,<br>Brightwater, FL 33990</address>
    <svg class="card__arc card__arc--bottom" viewBox="0 0 275 16" aria-hidden="true">
      <path d="M68 16 Q137 -8 207 16 Z" fill="var(--red)"/>
    </svg>
  </section>

  <section class="card card--back" aria-label="Business card back">
    <div class="brand">
      <span class="brand__dot" aria-hidden="true"></span>
      <span class="brand__name">redmesa garlic</span>
    </div>
  </section>
</main>
</body>
</html>
```